Local Roofing/Construction company business needs new biz card design

We need a new business card design, current cards are from the start of this operation and generic at best. We are a local Construction Company (General Contractor) with a majority of our work originating from insurance claims-exterior finish work is the main focus (Roofs-Siding-Gutters etc). Heavily involved with homeowners and the low ball offers they receive from insurance company's after a insurable event takes place. I have attached some of our original logo file(s) below.

```html
<!DOCTYPE html>
<html lang="en">
<head>
<meta charset="utf-8">
<title>Stoneward Construction – Business Card</title>
<link href="https://fonts.googleapis.com/css2?family=Poppins:wght@400;700&display=swap" rel="stylesheet">
<style>
  :root {
    --brand-green: #33d97a;
    --ink-dark: #0f1d1c;
    --paper: #ffffff;
    --backdrop: #e8e8e8;
    --text: #1c1c1c;
    --rule: #9a9a9a;
    --badge-text: #f7f3f0;
  }
  * { margin: 0; padding: 0; box-sizing: border-box; }
  html, body { width: 1200px; height: 1200px; overflow: hidden; }
  body {
    background: var(--backdrop);
    font-family: "Poppins", sans-serif;
    position: relative;
  }
  .card {
    position: absolute;
    top: 303px;
    height: 594px;
  }
  .card-front {
    left: 200px;
    width: 370px;
    background: var(--brand-green);
  }
  .front-badge {
    position: absolute;
    left: 40px;
    top: 475px;
    width: 285px;
    height: 74px;
    background: var(--ink-dark);
    clip-path: polygon(10px 0, calc(100% - 10px) 0, 100% 10px, 100% calc(100% - 10px), calc(100% - 10px) 100%, 10px 100%, 0 calc(100% - 10px), 0 10px);
    display: flex;
    align-items: center;
    justify-content: center;
    gap: 12px;
  }
  .front-badge .brand-square {
    width: 34px;
    height: 34px;
    background: var(--brand-green);
  }
  .front-badge .brand-name {
    color: var(--badge-text);
    font-weight: 700;
    font-size: 19px;
    line-height: 1.05;
    text-transform: uppercase;
    letter-spacing: 0.5px;
  }
  .card-back {
    left: 599px;
    width: 364px;
    background: var(--paper);
    text-align: center;
  }
  .back-brand {
    position: absolute;
    left: 0;
    right: 0;
    top: 60px;
    display: flex;
    flex-direction: column;
    align-items: center;
    gap: 16px;
  }
  .back-brand .brand-square {
    width: 120px;
    height: 120px;
    background: var(--brand-green);
  }
  .back-brand .brand-name {
    color: var(--brand-green);
    font-weight: 700;
    font-size: 24px;
    line-height: 1.1;
    text-transform: uppercase;
  }
  .person {
    position: absolute;
    left: 0; right: 0;
    top: 336px;
  }
  .person-name {
    color: var(--brand-green);
    font-weight: 700;
    font-size: 25px;
    line-height: 1.1;
    letter-spacing: 0.3px;
  }
  .person-role {
    color: var(--text);
    font-size: 16px;
    line-height: 1.2;
  }
  .contact-icons {
    position: absolute;
    left: 87px;
    right: 86px;
    top: 396px;
    display: flex;
    align-items: center;
    gap: 4px;
  }
  .contact-icons .rule { flex: 1; height: 1px; background: var(--rule); margin: 0 3px; }
  .icon {
    width: 25px;
    height: 25px;
    background: var(--brand-green);
    border-radius: 3px;
    display: flex;
    align-items: center;
    justify-content: center;
  }
  .contact-lines {
    position: absolute;
    left: 0; right: 0;
    top: 427px;
    color: var(--text);
    font-size: 16px;
    line-height: 21px;
  }
  .divider {
    position: absolute;
    left: 88px;
    right: 80px;
    top: 507px;
    height: 1px;
    background: var(--rule);
  }
  .address {
    position: absolute;
    left: 0; right: 0;
    top: 519px;
    color: var(--text);
    font-size: 16px;
    line-height: 21px;
  }
</style>
</head>
<body>
  <section class="card card-front">
    <div class="front-badge">
      <span class="brand-square"></span>
      <span class="brand-name">Stoneward<br>Construction</span>
    </div>
  </section>

  <section class="card card-back">
    <div class="back-brand">
      <span class="brand-square"></span>
      <span class="brand-name">Stoneward<br>Construction</span>
    </div>

    <div class="person">
      <p class="person-name">MARCUS HALE</p>
      <p class="person-role">Managing Director</p>
    </div>

    <div class="contact-icons">
      <span class="rule"></span>
      <span class="icon" aria-label="Phone">
        <svg width="15" height="15" viewBox="0 0 24 24" fill="#fff"><path d="M6.6 10.8a15.1 15.1 0 0 0 6.6 6.6l2.2-2.2a1 1 0 0 1 1-.25 11.4 11.4 0 0 0 3.6.57 1 1 0 0 1 1 1V20a1 1 0 0 1-1 1A17 17 0 0 1 3 4a1 1 0 0 1 1-1h3.5a1 1 0 0 1 1 1c0 1.25.2 2.45.57 3.57a1 1 0 0 1-.25 1z"/></svg>
      </span>
      <span class="icon" aria-label="Email">
        <svg width="16" height="12" viewBox="0 0 16 12" fill="none" stroke="#fff" stroke-width="1.3"><rect x="0.7" y="0.7" width="14.6" height="10.6"/><path d="M0.7 0.7 8 6.5 15.3 0.7M0.7 11.3 6 5.2M15.3 11.3 10 5.2"/></svg>
      </span>
      <span class="icon" aria-label="Website">
        <svg width="15" height="15" viewBox="0 0 16 16" fill="none" stroke="#fff" stroke-width="1.3"><circle cx="8" cy="8" r="6.8"/><ellipse cx="8" cy="8" rx="3" ry="6.8"/><path d="M1.2 8h13.6"/></svg>
      </span>
      <span class="rule"></span>
    </div>

    <div class="contact-lines">
      <p>044-987 650 312</p>
      <p>hello@stoneward.com</p>
      <p>www.stonewardbuild.com</p>
    </div>

    <div class="divider"></div>

    <div class="address">
      <p>18, Quarry Lane, Suite 4</p>
      <p>20931, Northvale</p>
    </div>
  </section>
</body>
</html>
```